Redesign of the UI of a customer service platform

To improve the user experience of our customers, we need a new design for our agent interface of our customer service platform (corvane.com).
The focus will be on the dashboard and the inbox screens (see attached) along with the common UI elements (Buttons, menu, fonts, forms...)
We want a simple and distinctive design

Target Market(s)

Worldwide

Industry/Entity Type

It Service

Number of Pages Required

3 page

Font styles to use
Sans Serif

Requirements
Must have
• New Onboarding page: this is a new page that is shown to user the first time they login to the platform. This will replace the current onboarding screen (setup SMS, Setup widget...etc)
• Dashboard page: to access important information and activate services (see screenshot from current site)
• Inbox page: to manage all the interactions with customers. (see screenshot from current site)
• UI elements (buttons, menus, forms, tables, fonts, color palette)

```html
<!DOCTYPE html>
<html lang="en">
<head>
<meta charset="utf-8">
<title>Corvane Agent Inbox</title>
<link href="https://fonts.googleapis.com/css2?family=Source+Sans+3:wght@400;600&display=swap" rel="stylesheet">
<style>
:root{
  --brand:#f15a2b;
  --sidebar:#2c3445;
  --sidebar-line:#3a4356;
  --sidebar-text:#ffffff;
  --sidebar-muted:#aeb5c2;
  --row-active:#ebedf0;
  --page:#eef0f3;
  --panel:#ffffff;
  --ink:#3d4249;
  --muted:#7b8088;
  --line:#e3e5e8;
  --nav-text:#7a7f86;
  --nav-icon:#b7bbc1;
  --badge-blue:#4db6e3;
  --badge-purple:#a58fd6;
  --bubble:#e5f3fa;
  --link:#e8472b;
  --ok:#7ccf78;
  --avatar:#c9b8a6;
  --avatar-dark:#8a7a6a;
}
*{box-sizing:border-box;margin:0;padding:0}
html,body{width:1200px;height:831px;overflow:hidden}
body{font-family:"Source Sans 3",sans-serif;background:var(--page);color:var(--ink);position:relative}

/* top bar */
.topbar{position:absolute;left:0;top:0;width:1200px;height:83px;background:#fff}
.brand{position:absolute;left:0;top:0;width:83px;height:83px;background:var(--brand);display:flex;align-items:center;justify-content:center;color:#fff;font-size:14px;font-weight:600}
.nav-item{position:absolute;top:0;width:84px;height:83px;border-right:1px solid #eceef0;text-align:center;color:var(--nav-text);font-size:13px}
.nav-item.is-active{background:#f3f4f6}
.nav-item svg{position:absolute;left:30px;top:14px}
.nav-item .label{position:absolute;left:0;right:0;top:52px}
.badge{position:absolute;top:17px;width:23px;height:23px;border-radius:50%;color:#fff;font-size:13px;font-weight:600;line-height:23px;text-align:center}
.agent-avatar{position:absolute;left:1132px;top:14px;width:55px;height:55px;border-radius:50%;background:linear-gradient(#d9c6b3,#7f8b99)}
.status-dot{position:absolute;left:1128px;top:15px;width:14px;height:14px;border-radius:50%;background:#6bc93f;border:2px solid #fff}

/* sidebar */
.sidebar{position:absolute;left:0;top:83px;width:343px;height:748px;background:var(--sidebar)}
.sidebar-head{height:83px;border-bottom:1px solid var(--sidebar-line);color:#fff;text-align:center;position:relative}
.sidebar-head h1{font-size:19px;font-weight:400;padding-top:18px}
.sidebar-head p{font-size:13px;color:var(--sidebar-muted);margin-top:1px}
.sidebar-head svg{position:absolute;right:15px;top:36px}
.conv{position:relative;height:84px;border-bottom:1px solid var(--sidebar-line);color:var(--sidebar-text)}
.conv.is-active{background:var(--row-active);color:var(--ink)}
.conv .avatar{position:absolute;left:14px;top:14px;width:55px;height:55px;border-radius:50%;background:linear-gradient(var(--avatar),var(--avatar-dark));border:2px solid #fff}
.conv .name{position:absolute;left:83px;top:20px;font-size:17px}
.conv .preview{position:absolute;left:83px;top:46px;font-size:13.5px;color:var(--sidebar-muted);display:flex;align-items:center;gap:6px}
.conv.is-active .preview{color:var(--muted)}
.conv .time{position:absolute;right:13px;top:13px;font-size:11.5px;color:var(--sidebar-muted)}
.conv.is-active .time{color:var(--muted)}
.mini{position:absolute;top:29px;width:28px;height:28px;border-radius:50%;background:linear-gradient(#d9c6b3,#7f8b99);border:2px solid #fff}
.channel-dot{width:8px;height:8px;border-radius:50%;background:var(--sidebar-muted)}

/* panels */
.panel{position:absolute;top:97px;height:720px;background:var(--panel)}
.profile{left:358px;width:412px}
.chat{left:774px;width:412px}
.btn{position:absolute;height:23px;border-radius:3px;font-size:13px;line-height:23px;padding-left:24px}
.btn-close{left:215px;top:15px;width:71px;background:var(--ok);color:#fff}
.btn-transfer{left:296px;top:15px;width:87px;background:#f1f2f4;color:#8d9299}
.btn svg{position:absolute;left:8px;top:6px}
.kebab{position:absolute;width:4px}
.kebab i{display:block;width:4px;height:4px;border-radius:50%;background:#9aa0a6;margin-bottom:3px}
.profile-photo{position:absolute;left:151px;top:66px;width:110px;height:110px;border-radius:50%;background:linear-gradient(#cfd6dd,#7d8894)}
.profile-name{position:absolute;left:0;right:0;top:184px;text-align:center;font-size:17px}
.profile-meta{position:absolute;left:0;right:0;top:218px;text-align:center;font-size:13.5px;color:var(--muted);display:flex;justify-content:center;gap:16px}
.profile-meta span{display:flex;align-items:center;gap:7px}
.rule{position:absolute;left:13px;right:14px;height:1px;background:var(--line)}
.section-title{position:absolute;left:13px;font-size:17px}
.add{position:absolute;right:14px;font-size:13px;color:var(--muted)}
.field{position:absolute;left:0;width:412px;height:18px;font-size:13.5px}
.field .k{position:absolute;right:309px;color:var(--muted)}
.field .v{position:absolute;left:121px}
.field .v.link{color:var(--link)}
.field svg{position:absolute;left:384px;top:2px}
.show-all{position:absolute;left:0;right:0;top:480px;text-align:center;color:var(--link);font-size:13.5px}
.task{position:absolute;left:13px;width:386px;height:18px;font-size:13.5px}
.task .date{position:absolute;left:246px}
.task svg{position:absolute;top:2px}
.empty{position:absolute;left:0;right:0;top:685px;text-align:center;font-size:13.5px;color:var(--muted)}

/* chat */
.bubble{position:absolute;background:var(--bubble);border-radius:3px;font-size:13.5px;line-height:20px;padding:2px 9px;color:var(--ink)}
.face{position:absolute;width:56px;height:56px;border-radius:50%;background:linear-gradient(#d7c4b1,#7b8795)}
.stamp{position:absolute;font-size:11.5px;color:var(--muted)}
.composer-tools{position:absolute;right:16px;top:607px;display:flex;gap:8px}
.composer{position:absolute;left:16px;top:645px;font-size:13.5px;color:var(--muted)}
</style>
</head>
<body>

<header class="topbar">
  <div class="brand">corvane</div>

  <div class="nav-item is-active" style="left:83px">
    <svg width="26" height="26" viewBox="0 0 26 26"><path d="M2 14h7l2 3h4l2-3h7v9H2z" fill="var(--nav-icon)"/><path d="M5 6h16l3 7h-7l-2 3h-4l-2-3H2z" fill="#cfd2d6"/></svg>
    <span class="badge" style="left:46px;background:var(--badge-blue)">4</span>
    <span class="label">Inbox</span>
  </div>
  <div class="nav-item" style="left:168px">
    <svg width="26" height="26" viewBox="0 0 26 26"><rect x="3" y="3" width="18" height="20" rx="2" fill="none" stroke="var(--nav-icon)" stroke-width="2"/><path d="M7 9h10M7 13h10M7 17h6" stroke="var(--nav-icon)" stroke-width="2"/></svg>
    <span class="badge" style="left:46px;background:var(--badge-purple)">1</span>
    <span class="label">Tasks</span>
  </div>
  <div class="nav-item" style="left:252px">
    <svg width="26" height="26" viewBox="0 0 26 26"><circle cx="13" cy="8" r="6" fill="var(--nav-icon)"/><path d="M2 25c0-7 5-10 11-10s11 3 11 10z" fill="var(--nav-icon)"/></svg>
    <span class="label">Customers</span>
  </div>
  <div class="nav-item" style="left:336px">
    <svg width="28" height="26" viewBox="0 0 28 26"><path d="M2 3l24 10L2 23l4-10z" fill="none" stroke="var(--nav-icon)" stroke-width="2" stroke-linejoin="round"/><path d="M6 13h20" stroke="var(--nav-icon)" stroke-width="2"/></svg>
    <span class="label">Campaigns</span>
  </div>
  <div class="nav-item" style="left:420px">
    <svg width="26" height="28" viewBox="0 0 26 28"><text x="13" y="23" text-anchor="middle" font-size="26" fill="var(--nav-icon)" font-family="Source Sans 3, sans-serif">$</text></svg>
    <span class="label">Payments</span>
  </div>
  <div class="nav-item" style="left:504px">
    <svg width="26" height="26" viewBox="0 0 26 26"><path d="M3 2v23M9 8v17M15 4v21M21 12v13" stroke="var(--nav-icon)" stroke-width="3"/></svg>
    <span class="label">Reports</span>
  </div>
  <div class="nav-item" style="left:588px">
    <svg width="26" height="26" viewBox="0 0 26 26"><circle cx="13" cy="13" r="8" fill="none" stroke="var(--nav-icon)" stroke-width="5" stroke-dasharray="4 2.3"/><circle cx="13" cy="13" r="6" fill="var(--nav-icon)"/><circle cx="13" cy="13" r="2.5" fill="#fff"/></svg>
    <span class="label">Settings</span>
  </div>

  <div class="agent-avatar" role="img" aria-label="Signed-in agent profile photo"></div>
  <div class="status-dot"></div>
</header>

<aside class="sidebar">
  <div class="sidebar-head">
    <h1>Open Conversations</h1>
    <p>New or Assigned to me</p>
    <svg width="14" height="9" viewBox="0 0 14 9"><path d="M1 1l6 6 6-6" fill="none" stroke="#fff" stroke-width="2"/></svg>
  </div>

  <div class="conv">
    <div class="avatar" role="img" aria-label="Customer photo of Clara Benet"></div>
    <div class="name">Clara Benet</div>
    <div class="preview"><svg width="13" height="12" viewBox="0 0 13 12"><path d="M0 5l13-5-3 12-4-4z" fill="currentColor"/></svg>Yes that would be great, please…</div>
    <div class="time">2 mins ago</div>
    <div class="mini" style="left:303px" role="img" aria-label="Assigned agent photo"></div>
  </div>

  <div class="conv is-active">
    <div class="avatar" role="img" aria-label="Customer photo of Daniel Morrow"></div>
    <div class="name">Daniel Morrow</div>
    <div class="preview"><svg width="14" height="12" viewBox="0 0 14 12"><rect x="0" y="0" width="14" height="9" fill="currentColor"/><rect x="4" y="10" width="6" height="2" fill="currentColor"/></svg>Hi, I need to know if there are…</div>
    <div class="time">9 mins ago</div>
    <div class="mini" style="left:303px" role="img" aria-label="Assigned agent photo"></div>
  </div>

  <div class="conv">
    <div class="avatar" role="img" aria-label="Customer photo of Owen Pryce"></div>
    <div class="name">Owen Pryce</div>
    <div class="preview"><span class="channel-dot"></span>The issue occured one more…</div>
    <div class="time">1 mins ago</div>
    <div class="mini" style="left:303px" role="img" aria-label="Assigned agent photo"></div>
  </div>

  <div class="conv">
    <div class="avatar" role="img" aria-label="Customer photo of Daniel Morrow"></div>
    <div class="name">Daniel Morrow</div>
    <div class="preview"><svg width="14" height="11" viewBox="0 0 14 11"><path d="M5 0L0 5l5 5V7c4 0 7 1 9 4-1-5-4-7-9-7z" fill="currentColor"/></svg>Yes that’s true we are not…</div>
    <div class="time">2 mins ago</div>
    <div class="mini" style="left:272px" role="img" aria-label="Second agent photo"></div>
    <div class="mini" style="left:303px" role="img" aria-label="Assigned agent photo"></div>
  </div>

  <div class="conv">
    <div class="avatar" role="img" aria-label="Customer photo of Clara Benet"></div>
    <div class="name">Clara Benet</div>
    <div class="preview"><svg width="13" height="12" viewBox="0 0 13 12"><path d="M0 5l13-5-3 12-4-4z" fill="currentColor"/></svg>Yes that would be great, please…</div>
    <div class="time">3 mins ago</div>
    <div class="mini" style="left:303px" role="img" aria-label="Assigned agent photo"></div>
  </div>
</aside>

<section class="panel profile">
  <div class="btn btn-close"><svg width="12" height="10" viewBox="0 0 12 10"><path d="M1 5l3.5 3.5L11 1" fill="none" stroke="#fff" stroke-width="2.4"/></svg>Close</div>
  <div class="btn btn-transfer"><svg width="12" height="10" viewBox="0 0 12 10"><path d="M0 5h9M6 1l4 4-4 4" fill="none" stroke="#9aa0a6" stroke-width="2"/></svg>Transfer</div>
  <div class="kebab" style="left:397px;top:18px"><i></i><i></i><i></i></div>

  <div class="profile-photo" role="img" aria-label="Profile photo of Daniel Morrow"></div>
  <div class="profile-name">Daniel Morrow</div>
  <div class="profile-meta">
    <span><svg width="15" height="12" viewBox="0 0 15 12"><rect x="0" y="0" width="15" height="9" fill="#b0b4ba"/><rect x="5" y="10" width="5" height="2" fill="#b0b4ba"/></svg>Campaigns</span>
    <span><svg width="11" height="14" viewBox="0 0 11 14"><path d="M5.5 0A5.5 5.5 0 0 0 0 5.5C0 9 5.5 14 5.5 14S11 9 11 5.5A5.5 5.5 0 0 0 5.5 0z" fill="#b0b4ba"/><circle cx="5.5" cy="5.5" r="2" fill="#fff"/></svg>United States</span>
  </div>

  <div class="rule" style="top:264px"></div>
  <div class="section-title" style="top:280px">Details</div>
  <div class="add" style="top:285px">+ ADD</div>

  <div class="field" style="top:331px"><span class="k">#ID :</span><span class="v">41</span><svg width="14" height="14" viewBox="0 0 14 14"><path d="M1 13l1-4 8-8 3 3-8 8z" fill="#b5b9be"/></svg></div>
  <div class="field" style="top:355px"><span class="k">Email :</span><span class="v link">daniel.morrow@postly.net</span><svg width="14" height="14" viewBox="0 0 14 14"><path d="M1 13l1-4 8-8 3 3-8 8z" fill="#b5b9be"/></svg></div>
  <div class="field" style="top:379px"><span class="k">Phone :</span><span class="v link">+1(555)210 4837</span><svg width="14" height="14" viewBox="0 0 14 14"><path d="M1 13l1-4 8-8 3 3-8 8z" fill="#b5b9be"/></svg></div>
  <div class="field" style="top:403px"><span class="k">Address Line 1 :</span><span class="v">4816 Larkspur Hollow Road</span><svg width="14" height="14" viewBox="0 0 14 14"><path d="M1 13l1-4 8-8 3 3-8 8z" fill="#b5b9be"/></svg></div>
  <div class="field" style="top:427px"><span class="k">City :</span><span class="v">Linden Falls</span><svg width="14" height="14" viewBox="0 0 14 14"><path d="M1 13l1-4 8-8 3 3-8 8z" fill="#b5b9be"/></svg></div>
  <div class="field" style="top:451px"><span class="k">State :</span><span class="v">Oregon</span><svg width="14" height="14" viewBox="0 0 14 14"><path d="M1 13l1-4 8-8 3 3-8 8z" fill="#b5b9be"/></svg></div>

  <div class="show-all"><svg width="11" height="8" viewBox="0 0 11 8"><path d="M1 1l4.5 4.5L10 1" fill="none" stroke="var(--link)" stroke-width="1.8"/></svg> Show All</div>

  <div class="rule" style="top:511px"></div>
  <div class="section-title" style="top:527px">Tasks</div>
  <div class="add" style="top:532px">+ ADD</div>
  <div class="task" style="top:564px">Verify customer identity<span class="date">2017-15-01</span>
    <svg style="left:336px" width="16" height="12" viewBox="0 0 16 12"><path d="M1 6l4.5 4.5L15 1" fill="none" stroke="#b5b9be" stroke-width="2.4"/></svg>
    <svg style="left:375px" width="12" height="14" viewBox="0 0 12 14"><rect x="0" y="1" width="12" height="2" fill="#b5b9be"/><rect x="1.5" y="4" width="9" height="10" fill="#b5b9be"/></svg>
  </div>
  <div class="task" style="top:588px">Check if the customer was billed twice<span class="date">2017-16-01</span>
    <svg style="left:336px" width="16" height="12" viewBox="0 0 16 12"><path d="M1 6l4.5 4.5L15 1" fill="none" stroke="#b5b9be" stroke-width="2.4"/></svg>
    <svg style="left:357px" width="12" height="12" viewBox="0 0 12 12"><path d="M1 1l10 10M11 1L1 11" stroke="#b5b9be" stroke-width="2"/></svg>
    <svg style="left:375px" width="12" height="14" viewBox="0 0 12 14"><rect x="0" y="1" width="12" height="2" fill="#b5b9be"/><rect x="1.5" y="4" width="9" height="10" fill="#b5b9be"/></svg>
  </div>

  <div class="rule" style="top:632px"></div>
  <div class="section-title" style="top:648px">Notes</div>
  <div class="add" style="top:653px">+ ADD</div>
  <div class="empty">Empty</div>
</section>

<section class="panel chat">
  <div class="kebab" style="left:396px;top:18px"><i></i><i></i><i></i></div>

  <div class="face" style="left:14px;top:37px" role="img" aria-label="Customer photo"></div>
  <div class="bubble" style="left:84px;top:43px">Hello</div>
  <div class="bubble" style="left:84px;top:72px;width:258px">My CC got billed twice on subscription renewal!</div>

  <div class="face" style="left:343px;top:166px" role="img" aria-label="Agent photo"></div>
  <div class="bubble" style="right:86px;top:173px">Hi Daniel</div>
  <div class="bubble" style="right:86px;top:199px;width:250px">Cay you please give me the last four digits of your CC?</div>
  <div class="bubble" style="right:86px;top:248px">I need that for verification purposes</div>

  <div class="face" style="left:14px;top:322px" role="img" aria-label="Customer photo"></div>
  <div class="bubble" style="left:84px;top:329px">Ok, here you go 5411</div>

  <div class="face" style="left:343px;top:401px" role="img" aria-label="Agent photo"></div>
  <div class="bubble" style="right:86px;top:408px">I will let billing know about this</div>

  <div class="face" style="left:14px;top:481px" role="img" aria-label="Customer photo"></div>
  <div class="bubble" style="left:84px;top:487px;width:258px">Yes that would be great, please do this ASAP</div>
  <div class="stamp" style="left:84px;top:538px">2 mins ago</div>

  <div class="composer-tools">
    <svg width="14" height="16" viewBox="0 0 14 16"><text x="7" y="14" text-anchor="middle" font-size="17" fill="#b0b4ba" font-family="Source Sans 3, sans-serif">$</text></svg>
    <svg width="12" height="16" viewBox="0 0 12 16"><path d="M8 4v8a2.5 2.5 0 0 1-5 0V3a1.8 1.8 0 0 1 3.6 0v8" fill="none" stroke="#b0b4ba" stroke-width="1.5"/></svg>
    <svg width="17" height="14" viewBox="0 0 17 14"><rect x="0.8" y="0.8" width="15.4" height="12.4" fill="none" stroke="#b0b4ba" stroke-width="1.5"/><path d="M2 12l4-5 3 3 2-2 4 4z" fill="#b0b4ba"/></svg>
    <svg width="16" height="16" viewBox="0 0 16 16"><circle cx="8" cy="8" r="7" fill="none" stroke="#b0b4ba" stroke-width="1.5"/><circle cx="5.5" cy="6" r="1" fill="#b0b4ba"/><circle cx="10.5" cy="6" r="1" fill="#b0b4ba"/><path d="M4.5 9.5a3.8 3.8 0 0 0 7 0" fill="none" stroke="#b0b4ba" stroke-width="1.4"/></svg>
  </div>
  <div class="rule" style="top:632px"></div>
  <div class="composer">Your Message...</div>
</section>

</body>
</html>
```